Stonebridge Building and Projects business cards

A business card with watermark background (construction work)

Company logo attached

Home improvement projects
House renovations
Bathroom and kitchen renovations
House extensions
New builds and granny flats

Director Omar Haddani
(Phone number)
omar@sbpbuilding.com.au
(Instagram logo) sbp_building

```html
<!DOCTYPE html>
<html lang="en">
<head>
<meta charset="utf-8">
<title>Stonebridge Building and Projects – Business Cards</title>
<link href="https://fonts.googleapis.com/css2?family=Montserrat:wght@600;700&family=Roboto:ital,wght@0,400;0,500;0,700;1,500&display=swap" rel="stylesheet">
<style>
  :root{
    --brand-blue:#1b78c6;
    --brand-blue-dark:#14609f;
    --charcoal:#3b3e43;
    --paper:#f7f8f9;
    --ink-muted:#4a4d52;
    --backdrop:#e4e6e9;
    --white:#ffffff;
  }
  *{box-sizing:border-box;margin:0;padding:0}
  html,body{width:1200px;height:1050px;overflow:hidden}
  body{background:var(--backdrop);font-family:"Roboto",Arial,sans-serif;position:relative}

  .card{position:absolute;width:620px;height:370px;border-radius:26px;overflow:hidden;
        box-shadow:0 14px 30px rgba(0,0,0,.18)}

  /* Front */
  .card-front{left:90px;top:110px;background:var(--brand-blue)}
  .front-logo{position:absolute;left:0;right:0;top:58px;text-align:center;color:var(--white)}
  .brand-mark{display:inline-block;width:22px;height:22px;background:var(--white);margin-bottom:14px}
  .brand-name{font-family:"Montserrat",Arial,sans-serif;font-weight:700;font-size:27px;line-height:1.2;letter-spacing:.2px}
  .tagline{display:inline-block;margin-top:10px;font-style:italic;font-weight:500;font-size:19px;
           border-top:2px solid currentColor;border-bottom:2px solid currentColor;padding:2px 10px}
  .services-band{position:absolute;left:0;right:0;top:228px;height:72px;background:var(--charcoal);
                 color:var(--white);display:flex;flex-direction:column;justify-content:center;align-items:center;
                 font-size:15px;line-height:1.6;letter-spacing:.2px}
  .services-band .sep{opacity:.8;margin:0 7px}
  .front-contacts{position:absolute;left:0;right:0;top:300px;height:70px;display:flex;justify-content:center;
                  align-items:center;gap:34px;color:var(--white);font-size:15px}
  .front-contacts span{display:flex;align-items:center;gap:8px}
  .dot-icon{width:14px;height:14px;border-radius:50%;border:2px solid var(--white)}

  /* Back */
  .card-back{left:490px;top:570px;background:var(--paper)}
  .card-back .wave{position:absolute;inset:0}
  .back-logo{position:absolute;left:36px;top:130px;width:300px;color:var(--brand-blue)}
  .back-logo .brand-mark{background:var(--brand-blue);margin-bottom:10px}
  .back-logo .brand-name{font-size:25px}
  .back-logo .tagline{color:var(--brand-blue);border-top:none;padding:2px 0;margin-top:8px}
  .person{position:absolute;right:40px;top:30px;text-align:right}
  .person-name{color:var(--brand-blue);font-weight:700;font-size:22px}
  .person-role{color:var(--ink-muted);font-size:14px;margin-top:2px}
  .back-contacts{position:absolute;right:36px;top:196px;list-style:none;color:var(--white);
                 font-size:15px;line-height:1.75;text-align:right}
  .back-contacts li{display:flex;justify-content:flex-end;align-items:center;gap:10px}
  .back-contacts svg{width:15px;height:15px;flex:none}
</style>
</head>
<body>

<section class="card card-front" aria-label="Business card front">
  <div class="front-logo">
    <span class="brand-mark"></span>
    <div class="brand-name">Stonebridge Building<br>and Projects</div>
    <div class="tagline">Built right, every time!</div>
  </div>
  <div class="services-band">
    <div>Home Improvement Projects<span class="sep">|</span>House Renovations<span class="sep">|</span>House Extensions</div>
    <div>Bathroom &amp; Kitchen Renovations<span class="sep">|</span>New Builds &amp; Granny Flats</div>
  </div>
  <div class="front-contacts">
    <span><i class="dot-icon"></i>sbp_building</span>
    <span>
      <svg width="16" height="16" viewBox="0 0 16 16" fill="none" stroke="#fff" stroke-width="1.4"><circle cx="8" cy="8" r="6.5"/><ellipse cx="8" cy="8" rx="3" ry="6.5"/><path d="M1.5 8h13"/></svg>
      sbpbuilding.com.au
    </span>
  </div>
</section>

<section class="card card-back" aria-label="Business card back">
  <svg class="wave" viewBox="0 0 620 370" preserveAspectRatio="none">
    <path d="M620 104 C510 112 450 140 405 200 C345 290 230 336 0 342 L0 370 L620 370 Z" fill="var(--brand-blue)"/>
    <path d="M620 88 C500 98 435 128 390 190 C330 276 240 318 70 330" fill="none" stroke="var(--charcoal)" stroke-width="8" stroke-linecap="round"/>
  </svg>
  <div class="person">
    <div class="person-name">Omar Haddani</div>
    <div class="person-role">Managing Director</div>
  </div>
  <div class="back-logo">
    <span class="brand-mark"></span>
    <div class="brand-name">Stonebridge Building and Projects</div>
    <div class="tagline">Built right, every time!</div>
  </div>
  <ul class="back-contacts">
    <li>0400 318 726
      <svg viewBox="0 0 16 16" fill="none" stroke="#fff" stroke-width="1.4"><circle cx="8" cy="8" r="7"/><path d="M5.5 4.5l1.5 1.5-1 1.2c.6 1.2 1.6 2.2 2.8 2.8l1.2-1 1.5 1.5-1 1c-2.5-.3-5.2-3-5.5-5.5z" fill="#fff" stroke="none"/></svg></li>
    <li>sbp_building
      <svg viewBox="0 0 16 16" fill="none" stroke="#fff" stroke-width="1.6"><circle cx="8" cy="8" r="6"/></svg></li>
    <li>omar@sbpbuilding.com.au
      <svg viewBox="0 0 16 16" fill="none" stroke="#fff" stroke-width="1.4"><rect x="1.5" y="3.5" width="13" height="9" rx="1"/><path d="M1.5 4l6.5 5 6.5-5"/></svg></li>
    <li>www.sbpbuilding.com.au
      <svg viewBox="0 0 16 16" fill="none" stroke="#fff" stroke-width="1.4"><circle cx="8" cy="8" r="6.5"/><ellipse cx="8" cy="8" rx="3" ry="6.5"/><path d="M1.5 8h13"/></svg></li>
  </ul>
</section>

</body>
</html>
```